Fenwick Grading LTD - website for irrigation & Landscape Lighting & Buried service wire

Looking for a website to help promote my business with Irrigation (installation, service, etc) and buried service wire/drainage solutions.

Commercial/Residential

Landscape lighting.

I’ll get photos in the trucks and trailers to upload as well maybe the machine as well.

Target Market(s)

Homeowners who want green grass and beautiful gardens. Beautiful landscape lighting

Industry/Entity Type

Irrigation systems and landscape lighting and buried service wire to homes and offering Drainage soltions.

Coding

Coded - Design and coding required

Number of Pages Required

4 page

Colors
F0912C
F2A743
F7CA91
FBE8D2
FDF5EE

Requirements
Must have
• was hoping to link up my email on fenwickgrading@mailbox-example.net with the website if possible.
Nice to have
• Page for Irrigation, page for landscape lighting, page buried service wire & drainage soltions.

```html
<!DOCTYPE html>
<html lang="en">
<head>
<meta charset="utf-8">
<title>Fenwick Grading LTD</title>
<link href="https://fonts.googleapis.com/css2?family=Poppins:wght@400;500;600;700&display=swap" rel="stylesheet">
<style>
:root{
  --orange:#F0912C;
  --orange-2:#F2A743;
  --orange-3:#F7CA91;
  --cream:#FBE8D2;
  --cream-2:#FDF5EE;
  --ink:#1c1c1c;
  --text:#555;
  --dark:#151515;
  --white:#fff;
}
*{box-sizing:border-box;margin:0;padding:0}
html,body{width:1200px;height:3896px;overflow:hidden}
body{font-family:"Poppins",sans-serif;color:var(--ink);background:var(--white);position:relative}
section,header,footer{position:absolute;left:0;width:1200px}
.btn{display:inline-block;background:var(--orange);color:var(--white);font-size:14px;font-weight:500;padding:12px 26px;border-radius:3px}

/* header + hero */
.hero{top:0;height:600px;background:linear-gradient(180deg,#1a1d14 0%,#2e3320 45%,#4a3b1c 80%,#2a2415 100%)}
.hero-photo{position:absolute;inset:0;background:radial-gradient(ellipse at 50% 70%,rgba(240,145,44,.35),transparent 60%)}
.nav{position:absolute;top:0;left:0;width:1200px;height:90px;display:flex;align-items:center;padding:0 56px}
.brand{color:var(--white);font-weight:700;font-size:22px;display:flex;align-items:center;gap:10px;white-space:nowrap}
.brand .dot{width:14px;height:14px;background:var(--orange)}
.menu{margin-left:auto;display:flex;gap:30px;align-items:center;color:var(--white);font-size:14px;white-space:nowrap}
.hero-copy{position:absolute;top:220px;left:0;width:1200px;text-align:center;color:var(--white)}
.hero-copy h1{font-size:36px;font-weight:700;line-height:1.3;max-width:760px;margin:0 auto}
.hero-copy p{font-size:14px;max-width:760px;margin:18px auto 26px;opacity:.9}

/* services */
.services{top:600px;height:680px;text-align:center}
.title{font-size:40px;font-weight:600}
.services .title{margin-top:50px}
.lead{font-size:15px;color:var(--text);max-width:600px;margin:18px auto 0;line-height:1.7}
.cards{position:absolute;top:212px;left:144px;display:flex;gap:60px}
.card{width:260px;text-align:left;background:var(--white);box-shadow:0 6px 20px rgba(0,0,0,.08);padding-bottom:22px}
.card.raised{margin-top:-10px;box-shadow:0 10px 30px rgba(0,0,0,.16)}
.card .ph{height:210px}
.card h3{font-size:17px;font-weight:600;margin:18px 20px 8px;line-height:1.4}
.card p{font-size:13px;color:var(--text);margin:0 20px 10px;line-height:1.6}
.card a{font-size:13px;color:var(--orange);margin:0 20px;border-bottom:1px solid var(--orange)}

/* about */
.about{top:1280px;height:560px;background:linear-gradient(135deg,#6f8a5a 0%,#9fb0a8 40%,#b9c6cc 60%,#3f5d2c 100%)}
.about-box{position:absolute;left:612px;top:80px;width:440px;height:460px;background:rgba(15,15,15,.9);border-radius:6px;color:var(--white);padding:44px 36px}
.about-box small{font-size:17px;font-weight:500}
.about-box h2{font-size:32px;font-weight:600;margin:4px 0 24px}
.about-box p{font-size:13px;line-height:1.7;opacity:.85;margin-bottom:14px}

/* reviews */
.reviews{top:1920px;height:500px;text-align:center}
.reviews .title{margin-top:70px;font-size:36px}
.review{position:absolute;top:160px;width:440px;height:300px;background:var(--white);box-shadow:0 6px 22px rgba(0,0,0,.1);padding:100px 34px 0;border-bottom:4px solid var(--orange)}
.review .avatar{position:absolute;top:-10px;left:50%;margin-left:-40px;width:80px;height:80px;border-radius:50%;border:3px solid var(--orange);background:linear-gradient(#c9a27a,#8a6a4a)}
.review h4{font-size:20px;font-weight:600;margin-bottom:12px}
.review p{font-size:13px;color:var(--text);line-height:1.7}
.review .quote{position:absolute;right:24px;bottom:12px;font-size:60px;color:#ddd;line-height:1}
.arrow{position:absolute;top:290px;width:20px;height:20px}

/* expertise banner */
.expertise{top:2472px;height:388px;background:linear-gradient(180deg,#1e2a1c 0%,#2f3f28 60%,#1a2216 100%);text-align:center;color:var(--white)}
.expertise h2{font-size:32px;font-weight:600;line-height:1.35;max-width:760px;margin:80px auto 18px}
.expertise p{font-size:13px;max-width:700px;margin:0 auto 24px;opacity:.85;line-height:1.6}

/* contact */
.contact{top:2900px;height:570px}
.contact-card{position:absolute;left:220px;top:60px;width:760px;height:460px;background:var(--white);box-shadow:0 8px 30px rgba(0,0,0,.1);padding:40px 60px;text-align:center}
.contact-card h2{font-size:36px;font-weight:600}
.contact-card .sub{font-size:13px;color:var(--text);margin:4px 0 24px}
.grid{display:grid;grid-template-columns:1fr 1fr;gap:12px}
.field{height:42px;background:#f3f3f3;border:1px solid #e6e6e6;font-size:13px;color:#777;text-align:left;padding:12px 14px}
.field .req{color:var(--orange)}
.field.wide{grid-column:1/3;height:96px}
.submit{grid-column:1/3;background:var(--orange);color:var(--white);height:44px;font-size:14px;font-weight:500;display:flex;align-items:center;justify-content:center}

/* footer */
.footer{top:3472px;height:424px;background:var(--dark);color:var(--white)}
.chev{position:absolute;top:-58px;left:0}
.f-brand{position:absolute;top:40px;left:0;width:1200px;text-align:center;font-size:30px;font-weight:700;display:flex;justify-content:center;align-items:center;gap:10px}
.f-brand .dot{width:16px;height:16px;background:var(--orange)}
.f-menu{position:absolute;top:150px;width:1200px;display:flex;justify-content:center;gap:40px;font-size:14px}
.f-info{position:absolute;top:200px;left:200px;width:800px;display:flex;justify-content:space-between;border-top:1px solid #333;border-bottom:1px solid #333;padding:24px 0}
.info{display:flex;gap:12px;align-items:center;font-size:13px;line-height:1.5}
.info .ico{flex:none;width:36px;height:36px;border-radius:50%;background:#2a2a2a;display:flex;align-items:center;justify-content:center}
.info b{font-weight:600;display:block;font-size:14px}
.f-bottom{position:absolute;top:350px;left:200px;width:800px;display:flex;justify-content:space-between;align-items:center;font-size:12px;color:#aaa}
.socials{display:flex;gap:10px}
.socials span{width:30px;height:30px;border-radius:50%;border:1px solid #555}
</style>
</head>
<body>

<header class="hero">
  <div class="hero-photo" role="img" aria-label="Night-lit garden and home with landscape lighting"></div>
  <nav class="nav">
    <div class="brand"><span class="dot"></span>Fenwick Grading LTD</div>
    <div class="menu">
      <span>Home</span><span>Irrigation</span><span>Landscape Lighting</span><span>Buried Wire &amp; Drainage</span>
      <span class="btn">Contact Us</span>
    </div>
  </nav>
  <div class="hero-copy">
    <h1>Transform Your Outdoor Space With Our Expert Irrigation And Lighting Solutions</h1>
    <p>Get the perfect blend of form and function with our state-of-the-art irrigation systems and landscape lighting. Trust our experienced team to deliver top-quality installation for your home.</p>
    <span class="btn">Contact Us</span>
  </div>
</header>

<section class="services">
  <h2 class="title">Our Services</h2>
  <p class="lead">Lorem Ipsum is simply dummy text of the printing and typesetting industry. Lorem Ipsum has been the industry's standard dummy text ever since</p>
  <div class="cards">
    <div class="card">
      <div class="ph" role="img" aria-label="Sprinkler watering a green lawn" style="background:linear-gradient(#8fb6d8,#4f8a3a)"></div>
      <h3>Irrigation Systems</h3>
      <a>Learn More</a>
    </div>
    <div class="card raised">
      <div class="ph" role="img" aria-label="Garden path lit by landscape lights at dusk" style="background:linear-gradient(#2d3b4a,#6a5a2a)"></div>
      <h3>Landscape Lighting</h3>
      <p>Our landscape lighting solutions are designed to enhance the beauty and functionality of your outdoor space.</p>
      <a>Learn More</a>
    </div>
    <div class="card">
      <div class="ph" role="img" aria-label="Trench with buried service wire and drainage pipe" style="background:linear-gradient(#b8b2a8,#5a4a3a)"></div>
      <h3>Buried Service Wire &amp; Drainage</h3>
      <a>Learn More</a>
    </div>
  </div>
</section>

<section class="about" role="img" aria-label="House with a green lawn and garden beds">
  <div class="about-box">
    <small>About</small>
    <h2>Fenwick Grading LTD</h2>
    <p>Lorem ipsum dolor sit amet, consectetur adipiscing elit sed do eiusmod tempor incididunt ut labore et dolore magna aliqua. Ut enim ad minim veniam quis.</p>
    <p>Lorem ipsum dolor sit amet, consectetur adipiscing elit sed do eiusmod tempor incididunt ut labore et dolore magna aliqua. Ut enim ad minim veniam quis nostrud exercitation.</p>
    <p>Lorem ipsum dolor sit amet, consectetur adipiscing elit sed do eiusmod tempor incididunt ut labore.</p>
    <span class="btn">Contact Us</span>
  </div>
</section>

<section class="reviews">
  <h2 class="title">Customer Reviews</h2>
  <svg class="arrow" style="left:100px" viewBox="0 0 20 20"><path d="M13 3 6 10l7 7" fill="none" stroke="#F0912C" stroke-width="2"/></svg>
  <div class="review" style="left:140px">
    <div class="avatar" role="img" aria-label="Customer portrait"></div>
    <h4>Marcus Hale</h4>
    <p>Lorem Ipsum is simply dummy text of the printing and typesetting industry. Lorem Ipsum has been the industry's standard dummy text ever since the 1500s, when an unknown printer took a galley of type and scrambled it.</p>
    <span class="quote">&rdquo;</span>
  </div>
  <div class="review" style="left:620px">
    <div class="avatar" role="img" aria-label="Customer portrait"></div>
    <h4>Nora Finch</h4>
    <p>Lorem Ipsum is simply dummy text of the printing and typesetting industry. Lorem Ipsum has been the industry's standard dummy text ever since the 1500s, when an unknown printer took a galley of type and scrambled it.</p>
    <span class="quote">&rdquo;</span>
  </div>
  <svg class="arrow" style="left:1080px" viewBox="0 0 20 20"><path d="M7 3l7 7-7 7" fill="none" stroke="#F0912C" stroke-width="2"/></svg>
</section>

<section class="expertise" role="img" aria-label="Lit garden path at night">
  <h2>Expertise In Irrigation Systems, Landscape Lighting, And Buried Service Wire &amp; Drainage</h2>
  <p>Lorem ipsum dolor sit amet, consectetur adipiscing elit, sed do eiusmod tempor incididunt ut labore et dolore magna aliqua. Ut enim ad minim veniam, quis nostrud exercitation.</p>
  <span class="btn">Contact Us</span>
</section>

<section class="contact">
  <div class="contact-card">
    <h2>Contact Us</h2>
    <p class="sub">Lorem ipsum dolor sit amet consectetur adipiscing elit</p>
    <div class="grid">
      <div class="field">First Name<span class="req">*</span></div>
      <div class="field">Email Address<span class="req">*</span></div>
      <div class="field">Telephone<span class="req">*</span></div>
      <div class="field">Inquiry For<span class="req">*</span></div>
      <div class="field wide">Messages</div>
      <div class="submit">Submit Now</div>
    </div>
  </div>
</section>

<footer class="footer">
  <svg class="chev" width="1200" height="60" viewBox="0 0 1200 60"><path d="M0 58H480L600 18 720 58H1200V60H0Z" fill="#151515"/><path d="M440 58 600 4 760 58" fill="none" stroke="#F0912C" stroke-width="3"/></svg>
  <div class="f-brand"><span class="dot"></span>Fenwick Grading LTD</div>
  <div class="f-menu"><span>Home</span><span>Irrigation</span><span>Landscape Lighting</span><span>Buried Wire &amp; Drainage</span><span>Contact Us</span></div>
  <div class="f-info">
    <div class="info"><span class="ico"><svg width="16" height="16" viewBox="0 0 16 16"><path d="M8 1a5 5 0 0 0-5 5c0 4 5 9 5 9s5-5 5-9a5 5 0 0 0-5-5Zm0 7a2 2 0 1 1 0-4 2 2 0 0 1 0 4Z" fill="#F0912C"/></svg></span><span>48 Maple Ridge Road,<br>Lakeview, ON L4R 2K7</span></div>
    <div class="info"><span class="ico"><svg width="16" height="16" viewBox="0 0 16 16"><path d="M4 1 6 5 4.5 6.5a9 9 0 0 0 5 5L11 10l4 2-1 3C7 15 1 9 1 2Z" fill="#F0912C"/></svg></span><span><b>Phone</b>555-014-2290</span></div>
    <div class="info"><span class="ico"><svg width="16" height="16" viewBox="0 0 16 16"><rect x="1" y="3" width="14" height="10" fill="none" stroke="#F0912C" stroke-width="1.5"/><path d="M1 3l7 6 7-6" fill="none" stroke="#F0912C" stroke-width="1.5"/></svg></span><span><b>E-Mail</b>fenwickgrading@mailbox-example.net</span></div>
  </div>
  <div class="f-bottom">
    <span>&copy; 2024 Fenwick Grading LTD. All Rights Reserved.</span>
    <div class="socials"><span></span><span></span><span></span><span></span></div>
  </div>
</footer>

</body>
</html>
```